Business Card Design

New business card design

Target Market(s)

Residential & Commercial Property Managers

Industry/Entity Type

Plumbing Services

Contact Information for Business Card

Name - Rowan Keddle, title - Director, Phone Number - 0431 286 517, email - rowan@tbk-plumbing.com.au, Company ABN - 73 215 904 386,

Font styles to use
Sans Serif

Colors
0054AA
0677BA
7BADD7
CADEEF
E8F1F8

```html
<!DOCTYPE html>
<html lang="en">
<head>
<meta charset="utf-8">
<title>TBK Plumbing Services – Business Card</title>
<link href="https://fonts.googleapis.com/css2?family=Montserrat:wght@500&family=Roboto:wght@300;400&display=swap" rel="stylesheet">
<style>
  :root {
    --stage: #1a1b1d;
    --navy: #1e242b;
    --navy-teal: #12587c;
    --accent: #0aa3e6;
    --ink: #1e242b;
    --paper: #ffffff;
    --muted: #8a8580;
    --light: #f4f6f8;
  }
  * { margin: 0; padding: 0; box-sizing: border-box; }
  html, body {
    width: 1200px; height: 1015px; overflow: hidden;
    background: var(--stage);
  }
  .canvas {
    position: relative; width: 1200px; height: 1015px;
  }
  .card {
    position: absolute; left: 220px; width: 760px; height: 434px;
    overflow: hidden;
    box-shadow: 0 18px 40px rgba(0,0,0,.55);
  }
  .card--front {
    top: 40px;
    background: linear-gradient(200deg, var(--navy-teal) 0%, #1a3a4f 38%, var(--navy) 72%);
  }
  .card--back { top: 530px; background: var(--paper); }

  .wordmark {
    position: absolute; left: 0; right: 0; text-align: center;
    font-family: 'Roboto', sans-serif; font-weight: 300;
    letter-spacing: 2px; text-transform: lowercase;
  }
  .card--front .wordmark { top: 165px; font-size: 64px; color: var(--paper); }
  .card--front .wordmark-sub { top: 250px; font-size: 16px; letter-spacing: 14px; color: var(--paper); }

  .card-shapes { position: absolute; inset: 0; }

  .card--back .wordmark { top: 66px; font-size: 58px; color: var(--ink); }
  .card--back .wordmark-sub { top: 142px; font-size: 14px; letter-spacing: 13px; color: var(--muted); }

  .holder {
    position: absolute; left: 150px; top: 318px; text-align: right; width: 230px;
  }
  .holder-name {
    font-family: 'Montserrat', sans-serif; font-weight: 500;
    font-size: 26px; color: var(--accent); text-transform: uppercase; line-height: 1.1;
  }
  .holder-title {
    font-family: 'Roboto', sans-serif; font-weight: 300;
    font-size: 20px; color: var(--light);
  }
  .divider {
    position: absolute; left: 398px; top: 282px; width: 1px; height: 64px;
    background: rgba(255,255,255,.25);
  }
  .contacts {
    position: absolute; left: 418px; top: 270px; list-style: none;
    font-family: 'Roboto', sans-serif; font-weight: 300; font-size: 21px; color: var(--light);
  }
  .contacts li { display: flex; align-items: center; gap: 8px; line-height: 36px; }
  .contacts svg { width: 22px; height: 22px; flex: none; }
  .abn {
    position: absolute; left: 272px; top: 386px;
    font-family: 'Roboto', sans-serif; font-weight: 300; font-size: 21px; color: var(--light);
  }
</style>
</head>
<body>
<main class="canvas">

  <section class="card card--front" aria-label="Business card front">
    <p class="wordmark">tbk</p>
    <p class="wordmark wordmark-sub">plumbing services</p>
  </section>

  <section class="card card--back" aria-label="Business card back">
    <svg class="card-shapes" viewBox="0 0 760 434" aria-hidden="true">
      <polygon points="0,296 760,112 760,434 0,434" fill="var(--navy)"/>
      <line x1="0" y1="293" x2="760" y2="109" stroke="var(--accent)" stroke-width="8"/>
      <circle cx="736" cy="115" r="17" fill="var(--accent)" stroke="var(--paper)" stroke-width="3"/>
    </svg>

    <p class="wordmark">tbk</p>
    <p class="wordmark wordmark-sub">plumbing services</p>

    <div class="holder">
      <p class="holder-name">Rowan Keddle</p>
      <p class="holder-title">Director</p>
    </div>
    <span class="divider" aria-hidden="true"></span>

    <ul class="contacts">
      <li>
        <svg viewBox="0 0 24 24" aria-hidden="true"><path fill="var(--accent)" d="M6.6 10.8a15 15 0 0 0 6.6 6.6l2.2-2.2a1 1 0 0 1 1-.25 11.4 11.4 0 0 0 3.6.57 1 1 0 0 1 1 1V20a1 1 0 0 1-1 1A17 17 0 0 1 3 4a1 1 0 0 1 1-1h3.5a1 1 0 0 1 1 1c0 1.25.2 2.45.57 3.57a1 1 0 0 1-.25 1z"/></svg>
        0431 286 517
      </li>
      <li>
        <svg viewBox="0 0 24 24" aria-hidden="true"><path fill="var(--accent)" d="M2 5h20v14H2z"/><path d="M2 5l10 8 10-8" fill="none" stroke="var(--navy)" stroke-width="1.8"/></svg>
        rowan@tbk-plumbing.com.au
      </li>
    </ul>

    <p class="abn">Company ABN - 73 215 904 386</p>
  </section>

</main>
</body>
</html>
```